Coastline Premier Retreats Business Card Design

Design a business card for Coastline Premier Retreats. Look at the website for colors and reference. Card should have logo, name, title, office number, mobile number, email, URL and a tagline like, "Luxury Hotel & Resort Email Marketing" (This might change).

https://www.coastlinepremierretreats.example

The rest I will leave up to your imagination.

Contact Information for Business Card

Logo, name, title, office number, mobile number, email, URL and a tagline like, "Luxury Hotel & Resort Email Marketing" (This might change).

```html
<!DOCTYPE html>
<html lang="en">
<head>
<meta charset="utf-8">
<title>Coastline Premier Retreats – Business Card</title>
<link rel="stylesheet" href="https://fonts.googleapis.com/css2?family=Montserrat:wght@400;500;700&display=swap">
<style>
  :root {
    --backdrop: #3a3a3a;
    --ink: #1c1c1c;
    --paper: #ffffff;
    --accent: #f07c1a;
    --text: #2b2b2b;
  }
  * { margin: 0; padding: 0; box-sizing: border-box; }
  html, body { width: 1200px; height: 901px; overflow: hidden; }
  body {
    background: var(--backdrop);
    font-family: "Montserrat", sans-serif;
    position: relative;
  }
  .card {
    position: absolute;
    width: 540px;
    height: 309px;
    border-radius: 16px;
    overflow: hidden;
    box-shadow: 0 10px 24px rgba(0,0,0,.45);
  }
  /* Back side */
  .card-back {
    left: 40px; top: 296px;
    background: var(--ink);
  }
  .card-back .brand {
    position: absolute;
    left: 0; right: 0; top: 110px;
    text-align: center;
    color: var(--paper);
    font-weight: 700;
    font-size: 28px;
    letter-spacing: 1px;
    text-transform: uppercase;
  }
  .card-back .tagline {
    position: absolute;
    left: 0; right: 0; top: 232px;
    text-align: center;
    color: var(--accent);
    font-size: 14px;
    letter-spacing: .5px;
  }
  /* Front side */
  .card-front {
    left: 620px; top: 296px;
    background: var(--paper);
  }
  .card-front .brand {
    position: absolute;
    left: 26px; top: 118px;
    width: 240px;
    color: var(--ink);
    font-weight: 700;
    font-size: 18px;
    line-height: 1.2;
    text-transform: uppercase;
    letter-spacing: .5px;
  }
  .divider {
    position: absolute;
    left: 282px; top: 48px;
    width: 1px; height: 160px;
    background: var(--accent);
  }
  .contact {
    position: absolute;
    left: 300px; top: 40px;
    color: var(--text);
  }
  .contact .name {
    color: var(--accent);
    font-weight: 700;
    font-size: 22px;
    letter-spacing: .5px;
    text-transform: uppercase;
    line-height: 1;
  }
  .contact .role {
    font-size: 11px;
    margin: 4px 0 10px;
  }
  .contact ul { list-style: none; }
  .contact li {
    display: flex;
    align-items: center;
    gap: 6px;
    font-size: 9.5px;
    line-height: 17px;
    white-space: nowrap;
  }
  .contact li svg { width: 9px; height: 9px; fill: var(--accent); flex: none; }
  .contact .address {
    font-size: 9.5px;
    line-height: 14px;
    margin-top: 10px;
  }
  .footer-band {
    position: absolute;
    left: 0; bottom: 0;
    width: 540px; height: 64px;
  }
  .footer-band .tagline {
    position: absolute;
    left: 190px; right: 70px; top: 26px;
    text-align: center;
    color: var(--paper);
    font-size: 11px;
    letter-spacing: .4px;
  }
</style>
</head>
<body>

<section class="card card-back">
  <div class="brand">Coastline Premier Retreats</div>
  <div class="tagline">Luxury Hotel &amp; Resort Email Marketing</div>
</section>

<section class="card card-front">
  <div class="brand">Coastline Premier Retreats</div>

  <div class="divider"></div>

  <div class="contact">
    <div class="name">Daniel Reyes</div>
    <div class="role">CEO/Founder</div>
    <ul>
      <li><svg viewBox="0 0 10 10"><path d="M2.5 0h5a1 1 0 0 1 1 1v8a1 1 0 0 1-1 1h-5a1 1 0 0 1-1-1V1a1 1 0 0 1 1-1zm0 1.5v6h5v-6z"/></svg>555.214.3070</li>
      <li><svg viewBox="0 0 10 10"><path d="M1 3c1-2 7-2 8 0l-1 1.5-2-.5V3H4v1l-2 .5zM2 5h6l1 4H1z"/></svg>+34 600 482 731</li>
      <li><svg viewBox="0 0 10 10"><path d="M0 2h10v6H0zm1 1v.3l4 2.6 4-2.6V3z"/></svg>info@coastlinepremierretreats.example</li>
      <li><svg viewBox="0 0 10 10"><circle cx="5" cy="5" r="5"/></svg>www.coastlinepremierretreats.example</li>
    </ul>
    <div class="address">Po Box, 456 B Harbor Rd<br>North America, CB 10250</div>
  </div>

  <div class="footer-band">
    <svg width="540" height="64" viewBox="0 0 540 64">
      <line x1="0" y1="42" x2="172" y2="42" stroke="var(--accent)" stroke-width="2.5"/>
      <line x1="488" y1="42" x2="540" y2="42" stroke="var(--accent)" stroke-width="2.5"/>
      <path d="M0 50 H170 C180 50 180 18 196 18 H464 C480 18 480 50 490 50 H540 V64 H0 Z" fill="var(--ink)"/>
    </svg>
    <div class="tagline">Luxury Hotel &amp; Resort Email Marketing</div>
  </div>
</section>

</body>
</html>
```